Vardem Web, LLC. is the name of the company that will be an Internet startup working in E-commerce and

We are a new company and going to start the business by hiring people we need. We are on “Hiring Now…” status right now which we like to be displayed on the website homepage.
The website should allow us to start the hiring process with letting people see and apply for jobs posted on the website.

the company logo is attached.

Target Market(s)

Tech Job Seekers, Programmers, iOS and Android Developers, Software engineers, Graphic designers, QA engineers, Customer Service Reps,...

Industry/Entity Type

Internet

Number of Pages Required

5+ page

Font styles to use
Serif
Sans Serif

Colors

Designer to choose colors to be used in the design.

Requirements
Must have
• We need a system to help job seekers to upload the resume and cover letter and fill the required forms and answer some questions on a form designed to evaluate the job seekers and let them know if they fit in the position and should apply for it.
• We also want job seekers to do a Pre-Employment Tests including Aptitude, Personality, and Skills after they qualified for a job which links our website to web-based pre-employment testing services websites like (Talvexa, Plivmark, Quorvane & Associates, Dunholt Assessment, …)

```html
<!DOCTYPE html>
<html lang="en">
<head>
<meta charset="utf-8">
<title>Vardem Web — Hiring Now</title>
<link href="https://fonts.googleapis.com/css2?family=Lato:wght@400;700;900&family=Open+Sans:wght@400;600;700&display=swap" rel="stylesheet">
<style>
:root{
  --orange:#ff5a00;
  --blue:#2b8ac6;
  --navy:#1f4e79;
  --dark:#2d2d2d;
  --ink:#333;
  --muted:#666;
  --light:#f1f1f1;
  --line:#d8d8d8;
  --white:#fff;
}
*{box-sizing:border-box;margin:0;padding:0}
html,body{width:1200px;height:3571px;overflow:hidden}
body{font-family:"Open Sans",Arial,sans-serif;color:var(--ink);background:var(--white);position:relative}
.section{position:absolute;left:0;width:1200px}
.wrap{position:absolute;left:98px;width:1004px}
h1,h2,h3,h4{font-family:"Lato",Arial,sans-serif}

/* header */
.topbar{top:0;height:105px;background:var(--white)}
.brand{position:absolute;left:98px;top:28px;display:flex;align-items:center;gap:12px}
.brand-mark{width:22px;height:22px;background:var(--orange);border-radius:50%}
.brand-name{font-family:"Lato",sans-serif;font-weight:900;font-size:40px;color:var(--blue);letter-spacing:-.5px}
.call{position:absolute;right:98px;top:26px;display:flex;gap:14px;align-items:center}
.call-icon{width:38px;height:38px;border:2px solid var(--blue);border-radius:50%;display:flex;align-items:center;justify-content:center}
.call small{display:block;font-size:15px;font-weight:600;color:var(--ink)}
.call strong{font-size:22px;color:var(--blue);font-weight:700}

.nav{top:105px;height:59px;background:var(--orange);display:flex;padding-left:98px}
.nav a{display:flex;align-items:center;justify-content:center;color:var(--white);text-decoration:none;font-size:15px;font-weight:600;height:59px;width:210px}
.nav a.active{background:#e04c00;width:124px}

/* hero */
.hero{top:164px;height:515px;background:linear-gradient(135deg,#3b4a5c 0%,#1d2a3a 55%,#2b3645 100%)}
.hero-photo{position:absolute;inset:0;background:radial-gradient(circle at 25% 40%,rgba(120,130,140,.35),transparent 55%),radial-gradient(circle at 70% 70%,rgba(60,80,100,.4),transparent 60%)}
.hero-copy{position:absolute;left:98px;top:168px;color:var(--white)}
.hero-copy h1{font-size:50px;font-weight:900;line-height:1.1}
.hero-copy h2{font-size:36px;font-weight:400;margin-top:14px}
.hero-copy p{font-size:17px;margin-top:24px}
.job-search{position:absolute;left:760px;top:117px;width:342px;height:279px;border:2px solid rgba(255,255,255,.8);background:rgba(20,70,120,.8);padding:26px 14px}
.job-search h3{text-align:center;color:var(--white);font-size:22px;font-weight:700;letter-spacing:.5px;margin-bottom:26px}
.field{display:block;background:var(--white);height:38px;border-radius:2px;margin-bottom:12px;font-size:13px;padding:10px;color:#555}
.js-buttons{display:flex;gap:16px;margin-top:10px}
.btn{display:inline-flex;align-items:center;justify-content:center;font-size:14px;font-weight:600;height:38px;padding:0 18px;border-radius:2px;text-decoration:none}
.btn-orange{background:var(--orange);color:var(--white);border:1px solid #fff}
.js-buttons .btn{flex:1}

.banner{top:679px;height:131px;background:var(--orange);color:var(--white);text-align:center;padding-top:30px}
.banner h2{font-size:31px;font-weight:700}
.banner p{font-size:16px;font-weight:600;margin-top:14px}

.title{text-align:center;font-family:"Lato",sans-serif;font-weight:900;font-size:28px;color:var(--blue);letter-spacing:.5px}
.title::after{content:"";display:block;width:96px;height:2px;background:var(--blue);margin:18px auto 0}

/* tests */
.tests{top:810px;height:642px}
.tests .title{position:absolute;top:70px;width:1200px}
.test-card{position:absolute;top:183px;width:486px;height:367px;border:1px solid var(--line);border-radius:6px;overflow:hidden;text-align:center;background:var(--white)}
.test-card header{height:60px;display:flex;align-items:center;justify-content:center;gap:40px;color:var(--white);font-family:"Lato",sans-serif;font-size:22px}
.test-card.aptitude{left:98px}
.test-card.aptitude header{background:var(--blue)}
.test-card.personality{left:614px}
.test-card.personality header{background:var(--orange)}
.test-card p{font-size:13px;line-height:1.55;color:var(--muted);padding:38px 60px 0}
.see-more{display:block;font-size:14px;font-weight:600;margin-top:22px}
.aptitude .see-more{color:var(--blue)}
.personality .see-more{color:var(--orange)}
.card-actions{display:flex;justify-content:center;gap:14px;margin-top:38px}
.btn-blue{background:var(--blue);color:var(--white)}
.btn-outline{border:2px solid var(--ink);color:var(--ink);background:var(--white)}

/* stats */
.stats{top:1452px;height:543px;background:linear-gradient(180deg,#1b1b1b,#2a2a2a 60%,#1f1f1f);color:var(--white);text-align:center}
.stats h2{font-size:29px;font-weight:900;margin-top:70px}
.stats h2::after{content:"";display:block;width:110px;height:2px;background:var(--white);margin:24px auto 0}
.stats p{font-size:14px;line-height:1.6;width:720px;margin:38px auto 0}
.stat{position:absolute;top:278px;width:148px;height:148px;border-radius:50%;border:4px solid var(--white);display:flex;flex-direction:column;align-items:center;justify-content:center}
.stat.blue{background:var(--blue)}
.stat.orange{background:var(--orange)}
.stat b{font-family:"Lato",sans-serif;font-size:36px;font-weight:900;line-height:1;margin-top:6px}
.stat span{font-size:14px;margin-top:4px}

/* audiences */
.audience{top:1995px;height:445px}
.aud-box{position:absolute;top:81px;width:486px;height:281px;padding:30px 28px;color:var(--white);box-shadow:0 0 0 5px #e6e6e6}
.aud-box.employers{left:98px;background:var(--blue)}
.aud-box.candidates{left:614px;background:var(--dark)}
.aud-box h3{font-size:22px;font-weight:900;display:flex;align-items:center;gap:12px}
.aud-box p{font-size:14px;line-height:1.6;margin-top:20px}
.aud-box .btn{background:var(--white);color:var(--ink);margin-top:24px;height:52px;padding:0 22px}

/* blog */
.blog{top:2440px;height:655px;background:var(--light)}
.blog .title{position:absolute;top:56px;width:1200px}
.post{position:absolute;top:155px;width:318px;text-align:center}
.post-photo{position:relative;height:226px;background:linear-gradient(135deg,#d9dde2,#9aa4ae)}
.date{position:absolute;left:0;bottom:0;width:50px;height:58px;color:var(--white);font-size:14px;display:flex;flex-direction:column;align-items:center;justify-content:center;line-height:1.5}
.date.orange{background:var(--orange)}
.date.dark{background:var(--dark)}
.post h4{font-size:19px;font-weight:700;margin-top:32px}
.post p{font-size:12px;line-height:1.6;color:var(--muted);margin:18px 16px 0}
.post .btn{margin-top:24px;height:40px;font-size:14px}

/* contact */
.contact{top:3095px;height:476px;border-top:4px solid var(--blue)}
.contact h2{position:absolute;left:98px;top:54px;color:var(--blue);font-size:28px;font-weight:900}
.contact h2::after{content:"";display:block;width:96px;height:2px;background:var(--blue);margin-top:10px}
.info{position:absolute;left:98px;display:flex;align-items:center;gap:24px;font-size:17px;line-height:1.6}
.info i{width:44px;height:44px;border:2px solid var(--orange);border-radius:50%;display:flex;align-items:center;justify-content:center;flex:none}
.info.pin i,.info.tel i{background:var(--orange)}
.form{position:absolute;left:484px;top:55px;width:618px}
.form h3{font-size:18px;font-weight:700;margin-bottom:22px}
.row{display:flex;gap:40px;margin-bottom:18px}
.input{flex:1;height:44px;border:2px solid #444;font-size:14px;padding:10px 8px;color:#555}
.input.area{height:86px}
.form .btn{height:38px}
.footer-line{position:absolute;left:98px;top:396px;width:1004px;height:1px;background:var(--line)}
.copy{position:absolute;top:420px;width:1200px;text-align:center;font-size:14px;font-weight:600}
</style>
</head>
<body>

<header class="section topbar">
  <div class="brand"><span class="brand-mark"></span><span class="brand-name">Vardem Web</span></div>
  <div class="call">
    <span class="call-icon"><svg width="18" height="18" viewBox="0 0 24 24"><path d="M6.6 10.8a15 15 0 006.6 6.6l2.2-2.2a1 1 0 011-.25 11.4 11.4 0 003.6.6 1 1 0 011 1V20a1 1 0 01-1 1A17 17 0 013 4a1 1 0 011-1h3.5a1 1 0 011 1c0 1.25.2 2.45.6 3.6a1 1 0 01-.25 1z" fill="#2b8ac6"/></svg></span>
    <div><small>Call Us Today!</small><strong>180 555 0147</strong></div>
  </div>
</header>

<nav class="section nav">
  <a class="active" href="#">HOME</a>
  <a href="#">APTITUDE TEST</a>
  <a href="#">PERSONALITY TEST</a>
  <a href="#">PRE-EMPLOYMENT TEST</a>
  <a href="#">CONTACT US</a>
</nav>

<section class="section hero">
  <div class="hero-photo" role="img" aria-label="Desk with calculator, glasses, plant and paperwork seen from above"></div>
  <div class="hero-copy">
    <h1>HIRING NOW</h1>
    <h2>Pre-Employment Tests</h2>
    <p>(Talvexa, Plivmark, Quorvane &amp; Associates, Dunholt Assessment</p>
  </div>
  <form class="job-search">
    <h3>JOB SEARCH</h3>
    <span class="field">Name</span>
    <span class="field">Email</span>
    <div class="js-buttons"><span class="btn btn-orange">Upload Resume</span><span class="btn btn-orange">Cover Letter</span></div>
  </form>
</section>

<section class="section banner">
  <h2>Know Who You're Hiring... BEFORE You Hire</h2>
  <p>We also want job seekers to do a Pre-Employment Tests including Aptitude, Personality, and Skills</p>
</section>

<section class="section tests">
  <h2 class="title">PRE-EMPLOYMENT TESTS</h2>
  <article class="test-card aptitude">
    <header><svg width="22" height="30" viewBox="0 0 22 30"><path d="M11 2a8 8 0 00-5 14v4h10v-4a8 8 0 00-5-14zM7 22h8v3H7z" fill="#fff"/></svg>Aptitude Test</header>
    <p>Nemo enim ipsam voluptatem quia voluptas sit aspernatur aut odit aut fugit, sed quia consequuntur magni dolores eos qui ratione volup tatem sequi nesciunt. Neque porro quisquam est, qui dolorem ipsum quia dolor sit amet, consectetur.</p>
    <span class="see-more">See More &gt;</span>
    <div class="card-actions"><span class="btn btn-blue">Read More</span><span class="btn btn-outline">See Sample Test</span></div>
  </article>
  <article class="test-card personality">
    <header><svg width="30" height="30" viewBox="0 0 30 30"><circle cx="15" cy="15" r="10" fill="none" stroke="#fff" stroke-width="3"/><path d="M15 15L26 4" stroke="#fff" stroke-width="3"/></svg>Personality and Skills Test</header>
    <p>Nemo enim ipsam voluptatem quia voluptas sit aspernatur aut odit aut fugit, sed quia consequuntur magni dolores eos qui ratione volup tatem sequi nesciunt. Neque porro quisquam est, qui dolorem ipsum quia dolor sit amet, consectetur.</p>
    <span class="see-more">See More &gt;</span>
    <div class="card-actions"><span class="btn btn-orange" style="border:none">Read More</span><span class="btn btn-outline">See Sample Test</span></div>
  </article>
</section>

<section class="section stats" role="img" aria-label="Dark background of people in a business meeting with site statistics">
  <h2>STATS OVERVIEW</h2>
  <p>Here's a brief overview of the website's stats. See how many jobs are posted, how many resumes are active and the number of present companies.</p>
  <div class="stat blue" style="left:114px">
    <svg width="40" height="34" viewBox="0 0 40 34"><rect x="2" y="8" width="36" height="24" rx="3" fill="#fff"/><rect x="14" y="2" width="12" height="8" fill="none" stroke="#fff" stroke-width="3"/></svg>
    <b>26</b><span>JOB OFFERS</span></div>
  <div class="stat orange" style="left:378px">
    <svg width="30" height="36" viewBox="0 0 30 36"><rect x="2" y="2" width="26" height="32" fill="#fff"/><path d="M7 10h16M7 16h16M7 22h16M7 28h10" stroke="#ff5a00" stroke-width="2"/></svg>
    <b>21</b><span>RESUMES</span></div>
  <div class="stat blue" style="left:640px">
    <svg width="34" height="36" viewBox="0 0 34 36"><rect x="4" y="2" width="20" height="32" fill="#fff"/><rect x="20" y="16" width="12" height="18" fill="#fff" stroke="#2b8ac6" stroke-width="2"/></svg>
    <b>17</b><span>COMPANIES</span></div>
  <div class="stat orange" style="left:914px">
    <svg width="44" height="32" viewBox="0 0 44 32"><circle cx="22" cy="9" r="7" fill="#fff"/><circle cx="8" cy="12" r="5" fill="#fff"/><circle cx="36" cy="12" r="5" fill="#fff"/><path d="M10 30a12 12 0 0124 0zM0 30a8 8 0 0112-7v7zM44 30a8 8 0 00-12-7v7z" fill="#fff"/></svg>
    <b>64</b><span>MEMBERS</span></div>
</section>

<section class="section audience">
  <article class="aud-box employers">
    <h3><svg width="28" height="24" viewBox="0 0 28 24"><rect x="1" y="6" width="26" height="17" rx="2" fill="none" stroke="#fff" stroke-width="2.5"/><rect x="9" y="1" width="10" height="6" fill="none" stroke="#fff" stroke-width="2.5"/></svg>EMPLOYERS</h3>
    <p>Neque porro quisquam est, qui dolorem ipsum quia dolor sit amet, consectetur, adipisci velit, sed quia non numquam eius modi tempora incidunt.</p>
    <span class="btn">Pre-Employment Tests</span>
  </article>
  <article class="aud-box candidates">
    <h3><svg width="32" height="24" viewBox="0 0 32 24"><circle cx="11" cy="7" r="6" fill="#fff"/><circle cx="23" cy="8" r="5" fill="#fff"/><path d="M0 23a11 11 0 0122 0zM18 23a9 9 0 0114-8v8z" fill="#fff"/></svg>CANDIDATES</h3>
    <p>Neque porro quisquam est, qui dolorem ipsum quia dolor sit amet, consectetur, adipisci velit, sed quia non numquam eius modi tempora incidunt.</p>
    <span class="btn">Pre-Employment Tests</span>
  </article>
</section>

<section class="section blog">
  <h2 class="title">BLOG POSTS</h2>
  <article class="post" style="left:98px">
    <div class="post-photo" role="img" aria-label="Job interview between two people at an office desk"><span class="date orange">JAN<br>17</span></div>
    <h4>Nemo enim ipsam</h4>
    <p>Sed ut perspiciatis unde omnis iste natus error sit voluptatem accusantium doloremque laudantium, totam rem aperiam.</p>
    <span class="btn btn-orange" style="border:none">Read More</span>
  </article>
  <article class="post" style="left:441px">
    <div class="post-photo" role="img" aria-label="Business handshake across a table in a bright office"><span class="date dark">DEC<br>21</span></div>
    <h4>Voluptatem quia voluptas</h4>
    <p>Sed ut perspiciatis unde omnis iste natus error sit voluptatem accusantium doloremque laudantium, totam rem aperiam.</p>
    <span class="btn btn-outline">Read More</span>
  </article>
  <article class="post" style="left:784px">
    <div class="post-photo" role="img" aria-label="Hand signing a contract with a pen"><span class="date dark">DEC<br>14</span></div>
    <h4>Aspernatur aut odit fugit</h4>
    <p>Sed ut perspiciatis unde omnis iste natus error sit voluptatem accusantium doloremque laudantium, totam rem aperiam.</p>
    <span class="btn btn-outline">Read More</span>
  </article>
</section>

<footer class="section contact">
  <h2>CONTACT US</h2>
  <div class="info" style="top:158px"><i><svg width="20" height="14" viewBox="0 0 20 14"><rect x="1" y="1" width="18" height="12" fill="none" stroke="#ff5a00" stroke-width="2"/><path d="M1 1l9 7 9-7" fill="none" stroke="#ff5a00" stroke-width="2"/></svg></i>info@vardemweb.com</div>
  <div class="info pin" style="top:226px"><i><svg width="16" height="22" viewBox="0 0 16 22"><path d="M8 1a7 7 0 00-7 7c0 5 7 13 7 13s7-8 7-13a7 7 0 00-7-7z" fill="#fff"/><circle cx="8" cy="8" r="2.5" fill="#ff5a00"/></svg></i><span>48 Kestrel Lane<br>Ashford, MD 2045</span></div>
  <div class="info tel" style="top:310px"><i><svg width="20" height="20" viewBox="0 0 24 24"><path d="M6.6 10.8a15 15 0 006.6 6.6l2.2-2.2a1 1 0 011-.25 11.4 11.4 0 003.6.6 1 1 0 011 1V20a1 1 0 01-1 1A17 17 0 013 4a1 1 0 011-1h3.5a1 1 0 011 1c0 1.25.2 2.45.6 3.6a1 1 0 01-.25 1z" fill="#fff"/></svg></i>180 555 0147</div>
  <form class="form">
    <h3>Fill out the form below, and we'll contact you shortly.</h3>
    <div class="row"><span class="input">First Name</span><span class="input">Last Name</span></div>
    <div class="row"><span class="input">Phone Number</span><span class="input">E-Mail Address</span></div>
    <div class="row"><span class="input area">Message</span></div>
    <span class="btn btn-orange" style="border:none">Send Now</span>
  </form>
  <div class="footer-line"></div>
  <p class="copy">2017 © Vardem Web. All rights reserved.</p>
</footer>

</body>
</html>
```